Dultavo.com webside

I want to build a Dultavo.com retail website use on Shopify, reselling three main categories: Office Supplies, Packing Supplies, and Home Consumables. I also wish the webpage has the same functions as the Zelvik home page. The page is split into three different parts with the top being a sliding screen showcasing promotion products, below it being the three categories, and finally, a moving screen showing company missions.
Target Market(s)
U.S online
Industry/Entity Type
Office Supplies, packing Supplies and Home Consumables
Coding
Coded - Design and coding required
Number of Pages Required
5+ page
Look and feel

```html
<!DOCTYPE html>
<html lang="en">
<head>
<meta charset="utf-8">
<title>Dultavo – Office, Packing &amp; Home Supplies</title>
<link rel="stylesheet" href="https://fonts.googleapis.com/css2?family=Poppins:wght@600;700&family=Roboto:wght@400;500;700&display=swap">
<style>
:root{
  --brand:#0ba585;
  --brand-dark:#08957a;
  --ink:#111111;
  --text:#555555;
  --muted:#666666;
  --line:#e2e2e2;
  --footer:#2c2c2c;
  --white:#ffffff;
}
*{box-sizing:border-box;margin:0;padding:0}
html,body{width:1200px;height:3724px;overflow:hidden}
body{position:relative;font-family:'Roboto',Arial,sans-serif;color:var(--ink);background:var(--white)}
.abs{position:absolute}
.heading{font-family:'Poppins',Arial,sans-serif;font-weight:700;text-align:center;color:var(--ink)}
.btn{display:flex;align-items:center;justify-content:center;gap:10px;background:var(--brand);color:var(--white);font-weight:700;font-size:15px;letter-spacing:.2px;border-radius:2px}

/* header */
.site-header{left:0;top:0;width:1200px;height:61px;background:var(--brand)}
.logo{left:111px;top:16px;font-family:'Roboto',sans-serif;font-weight:700;font-size:24px;color:var(--white);letter-spacing:.5px}
.main-nav{top:21px;left:0;width:1200px;font-size:14px;font-weight:700;color:var(--white)}
.main-nav span{position:absolute;white-space:nowrap}
.header-icons{left:1012px;top:20px;display:flex;gap:12px}

/* hero */
.hero{left:0;top:61px;width:1200px;height:556px;background:linear-gradient(180deg,#bfc2c4 0%,#a9acae 55%,#8d9092 100%)}
.hero-welcome{left:0;top:185px;width:1200px;text-align:center;font-family:'Poppins',sans-serif;font-weight:700;font-size:30px;color:var(--white)}
.hero-title{left:0;top:218px;width:1200px;text-align:center;font-family:'Poppins',sans-serif;font-weight:700;font-size:100px;line-height:1.1;color:var(--white)}
.hero .btn,.promo .btn{width:144px;height:46px}
.slider-arrow{width:38px;height:38px;border-radius:50%;background:var(--white);display:flex;align-items:center;justify-content:center}

/* categories */
.section-title{left:0;width:1200px;font-size:29px}
.intro{left:111px;top:738px;width:978px;text-align:center;font-size:16px;line-height:26px;color:var(--text)}
.category img,.photo{background:#ccc}
.category-photo{width:315px;height:287px}
.category-name{width:315px;text-align:center;font-size:19px;font-weight:500;color:var(--ink)}

/* about */
.about{left:0;top:1246px;width:1200px;height:515px;background:linear-gradient(90deg,#304550 0%,#9fa5a8 30%,#d7d9da 60%,#c4c7c9 100%)}
.about-card{left:111px;top:1324px;width:489px;height:343px;background:var(--white);padding:40px 37px}
.about-card h2{font-family:'Poppins',sans-serif;font-size:28px;line-height:34px;margin-bottom:8px}
.about-card p{font-size:14.3px;line-height:24px;color:var(--text);text-align:justify}

/* products */
.product-card{width:236px;height:246px;border:1px solid var(--line);display:flex;align-items:center;justify-content:center}
.product-shot{width:150px;height:150px;border-radius:4px}
.product-title{width:236px;text-align:center;font-size:17px;font-weight:700}
.product-price{width:236px;text-align:center;font-size:22px;font-weight:500;color:var(--brand)}

/* promo band */
.promo{left:0;top:2309px;width:1200px;height:386px;background:linear-gradient(180deg,#4a4d50 0%,#6e6a64 45%,#3d3e40 100%)}
.promo-text{left:0;top:2418px;width:1200px;text-align:center;font-family:'Poppins',sans-serif;font-weight:700;font-size:29px;line-height:39px;color:var(--white);text-transform:uppercase}

/* news */
.news-photo{width:315px;height:218px}
.news-body{width:315px;padding:0 17px}
.news-title{font-size:15.5px;font-weight:700;color:var(--ink)}
.news-date{margin-top:10px;font-size:14px;font-weight:500;color:var(--brand)}
.news-excerpt{margin-top:12px;font-size:13.3px;line-height:22px;color:var(--muted);text-align:justify}
.read-more{margin-top:10px;display:flex;align-items:center;gap:8px;font-size:12.5px;font-weight:700;color:var(--brand);text-decoration:underline}

/* footer */
.site-footer{left:0;top:3324px;width:1200px;height:400px;background:var(--footer);color:var(--white)}
.footer-heading{font-size:21px;font-weight:500;color:var(--white)}
.social{width:38px;height:38px;border:1.5px solid var(--white);border-radius:50%}
.footer-text{font-size:14px;line-height:22px;color:var(--white)}
.field{height:39px;background:var(--white);border:1px solid #ccc;font-size:13.5px;color:#777;padding:0 15px;display:flex;align-items:center}
.signup{height:39px;background:var(--brand);color:var(--white);font-weight:700;font-size:13.5px;display:flex;align-items:center;justify-content:center}
.pay-badge{width:32px;height:20px;border-radius:3px}
</style>
</head>
<body>

<!-- Header -->
<header class="abs site-header">
  <div class="abs logo">DULTAVO</div>
  <nav class="abs main-nav">
    <span style="left:430px">Home</span>
    <span style="left:502px">About</span>
    <span style="left:573px">Our Products</span>
    <span style="left:693px">Shop</span>
    <span style="left:759px">Contact</span>
  </nav>
  <div class="abs header-icons">
    <svg width="16" height="16" viewBox="0 0 16 16"><circle cx="6.5" cy="6.5" r="4.5" fill="none" stroke="#fff" stroke-width="2"/><line x1="10" y1="10" x2="14" y2="14" stroke="#fff" stroke-width="2.4" stroke-linecap="round"/></svg>
    <svg width="14" height="16" viewBox="0 0 14 16"><circle cx="7" cy="4.5" r="3.5" fill="#fff"/><path d="M1 15c0-4 2.5-6 6-6s6 2 6 6z" fill="#fff"/></svg>
    <svg width="17" height="16" viewBox="0 0 17 16"><path d="M0 1h3l2.4 9h9L16 4H4.5" fill="none" stroke="#fff" stroke-width="2"/><path d="M5 5h10l-1.5 4.5H6z" fill="#fff"/><circle cx="6.5" cy="13.5" r="1.6" fill="#fff"/><circle cx="13" cy="13.5" r="1.6" fill="#fff"/></svg>
  </div>
</header>

<!-- Hero slider -->
<section class="abs hero" role="img" aria-label="Bright modern office with glass walls, desks and computers"></section>
<div class="abs hero-welcome">Welcome To</div>
<div class="abs hero-title">Dultavo</div>
<a class="abs btn" style="left:528px;top:367px;width:144px;height:46px">SHOP NOW
  <svg width="14" height="12" viewBox="0 0 17 16"><path d="M0 1h3l2.4 9h9L16 4H4.5" fill="none" stroke="#fff" stroke-width="2"/><path d="M5 5h10l-1.5 4.5H6z" fill="#fff"/><circle cx="6.5" cy="13.5" r="1.6" fill="#fff"/><circle cx="13" cy="13.5" r="1.6" fill="#fff"/></svg></a>
<div class="abs slider-arrow" style="left:39px;top:286px"><svg width="10" height="16" viewBox="0 0 10 16"><path d="M8 2 2 8l6 6" fill="none" stroke="#111" stroke-width="2.2"/></svg></div>
<div class="abs slider-arrow" style="left:1123px;top:286px"><svg width="10" height="16" viewBox="0 0 10 16"><path d="M2 2l6 6-6 6" fill="none" stroke="#111" stroke-width="2.2"/></svg></div>

<!-- Categories -->
<h2 class="abs heading section-title" style="top:685px">CATEGORIES</h2>
<p class="abs intro">Lorem ipsum dolor sit amet, consectetur adipiscing elit, sed do eiusmod tempor incididunt ut labore et dolore magna aliqua. Ut enim ad minim veniam, quis nostrud exercitation ullamco laboris nisi ut aliquip ex ea commodo consequat.</p>

<div class="abs category-photo" style="left:111px;top:836px;background:linear-gradient(160deg,#8c9196,#c9cbcc 60%,#a7a39d)" role="img" aria-label="Office interior with rows of desks and monitors"></div>
<div class="abs category-photo" style="left:442px;top:836px;background:linear-gradient(160deg,#a99a86,#d8c3a3 55%,#b69774)" role="img" aria-label="Worker taping cardboard boxes for shipping"></div>
<div class="abs category-photo" style="left:773px;top:836px;background:linear-gradient(160deg,#d9d5d0,#e7e3de 40%,#35a9d8 75%,#d4cfc7)" role="img" aria-label="Blue bucket of cleaning products and brushes"></div>
<div class="abs category-name" style="left:111px;top:1141px">Office Supplies</div>
<div class="abs category-name" style="left:442px;top:1141px">Packing Supplies</div>
<div class="abs category-name" style="left:773px;top:1141px">Home Consumables</div>

<!-- About -->
<section class="abs about" role="img" aria-label="Open plan office with desks, chairs and large windows"></section>
<div class="abs about-card">
  <h2>ABOUT US</h2>
  <p>Lorem ipsum dolor sit amet, consectetur adipiscing elit, sed do eiusmod tempor incididunt ut labore et dolore magna aliqua. Ut enim ad minim veniam, quis nostrud exercitation ullamco laboris nisi ut aliquip ex ea commodo consequat. Duis aute irure dolor in reprehenderit in voluptate velit esse cillum dolore eu fugiat nulla pariatur. Excepteur sint occaecat cupidatat non proident, sunt in culpa qui officia deserunt mollit anim id est laborum Lorem ipsum dolor sit amet, consectetur adipiscing elit, sed do eiusmod tempor incididunt ut labore et dolore magna aliqua.</p>
</div>

<!-- Featured products -->
<h2 class="abs heading section-title" style="top:1840px">FEATURED PRODUCTS</h2>
<div class="abs product-card" style="left:107px;top:1920px"><div class="product-shot" style="background:linear-gradient(135deg,#fff 30%,#2a9fd8 50%,#fff 70%)" role="img" aria-label="Blue scrubbing brush"></div></div>
<div class="abs product-card" style="left:357px;top:1920px"><div class="product-shot" style="background:radial-gradient(ellipse at 50% 55%,#f0169a 30%,#fff 60%)" role="img" aria-label="Pink spray bottle"></div></div>
<div class="abs product-card" style="left:607px;top:1920px"><div class="product-shot" style="background:radial-gradient(circle,#fff 22%,#c9a57f 28%,#e6d2bb 50%,#fff 66%)" role="img" aria-label="Roll of brown packing tape"></div></div>
<div class="abs product-card" style="left:856px;top:1920px"><div class="product-shot" style="background:radial-gradient(ellipse at 50% 45%,#222 32%,#888 45%,#fff 62%)" role="img" aria-label="Black leather office chair"></div></div>
<div class="abs product-title" style="left:107px;top:2191px">Product Title</div>
<div class="abs product-title" style="left:357px;top:2191px">Product Title</div>
<div class="abs product-title" style="left:607px;top:2191px">Product Title</div>
<div class="abs product-title" style="left:856px;top:2191px">Product Title</div>
<div class="abs product-price" style="left:107px;top:2211px">$50.00</div>
<div class="abs product-price" style="left:357px;top:2211px">$50.00</div>
<div class="abs product-price" style="left:607px;top:2211px">$50.00</div>
<div class="abs product-price" style="left:856px;top:2211px">$50.00</div>

<!-- Promo band -->
<section class="abs promo" role="img" aria-label="Dim office with rows of desks, monitors and black chairs"></section>
<div class="abs promo-text">The target market is office supplies, packing<br>supplies and home consumables</div>
<a class="abs btn" style="left:528px;top:2529px;width:144px;height:46px">SHOP NOW
  <svg width="14" height="12" viewBox="0 0 17 16"><path d="M0 1h3l2.4 9h9L16 4H4.5" fill="none" stroke="#fff" stroke-width="2"/><path d="M5 5h10l-1.5 4.5H6z" fill="#fff"/><circle cx="6.5" cy="13.5" r="1.6" fill="#fff"/><circle cx="13" cy="13.5" r="1.6" fill="#fff"/></svg></a>

<!-- Latest news -->
<h2 class="abs heading section-title" style="top:2774px">LATEST NEWS</h2>
<div class="abs news-photo" style="left:113px;top:2853px;background:linear-gradient(160deg,#d8dcdc,#a9c3c6 50%,#e2c36a)" role="img" aria-label="Person holding a basket of cleaning supplies"></div>
<div class="abs news-photo" style="left:442px;top:2853px;background:linear-gradient(160deg,#6a6a68,#9a9894 45%,#e8e6e2)" role="img" aria-label="Desk with laptop, notebooks and rolled papers"></div>
<div class="abs news-photo" style="left:772px;top:2853px;background:linear-gradient(160deg,#eef0f2,#dfe3e8 50%,#c9a97a)" role="img" aria-label="Worker in white coat packing a cardboard box"></div>

<div class="abs news-body" style="left:113px;top:3094px">
  <div class="news-title">Lorem ipsum dolor sit amet, consec</div>
  <div class="news-date">01 Oct 2022</div>
  <p class="news-excerpt">Lorem ipsum dolor sit amet, consectetur adipiscing elit, sed eiusmod tempor incididunt ut labore et dolore magna aliqua.</p>
  <div class="read-more">READ MORE <svg width="11" height="11" viewBox="0 0 12 12"><circle cx="6" cy="6" r="6" fill="#0ba585"/><path d="M5 3.5 7.5 6 5 8.5" fill="none" stroke="#fff" stroke-width="1.6"/></svg></div>
</div>
<div class="abs news-body" style="left:442px;top:3094px">
  <div class="news-title">Lorem ipsum dolor sit amet, consec</div>
  <div class="news-date">01 Oct 2022</div>
  <p class="news-excerpt">Lorem ipsum dolor sit amet, consectetur adipiscing elit, sed eiusmod tempor incididunt ut labore et dolore magna aliqua.</p>
  <div class="read-more">READ MORE <svg width="11" height="11" viewBox="0 0 12 12"><circle cx="6" cy="6" r="6" fill="#0ba585"/><path d="M5 3.5 7.5 6 5 8.5" fill="none" stroke="#fff" stroke-width="1.6"/></svg></div>
</div>
<div class="abs news-body" style="left:772px;top:3094px">
  <div class="news-title">Lorem ipsum dolor sit amet, consec</div>
  <div class="news-date">01 Oct 2022</div>
  <p class="news-excerpt">Lorem ipsum dolor sit amet, consectetur adipiscing elit, sed eiusmod tempor incididunt ut labore et dolore magna aliqua.</p>
  <div class="read-more">READ MORE <svg width="11" height="11" viewBox="0 0 12 12"><circle cx="6" cy="6" r="6" fill="#0ba585"/><path d="M5 3.5 7.5 6 5 8.5" fill="none" stroke="#fff" stroke-width="1.6"/></svg></div>
</div>

<!-- Footer -->
<footer class="abs site-footer">
  <div class="abs footer-heading" style="left:111px;top:62px">Follow Us On</div>
  <div class="abs social" style="left:111px;top:111px"></div>
  <div class="abs social" style="left:159px;top:111px"></div>
  <div class="abs social" style="left:208px;top:111px"></div>
  <p class="abs footer-text" style="left:112px;top:173px;width:440px">Lorem ipsum dolor sit amet, consectetur adipiscing elit, sed do eiusmod tempor incididunt ut labore et dolore magna</p>

  <div class="abs footer-heading" style="left:603px;top:62px">Signup Newsletter</div>
  <p class="abs footer-text" style="left:603px;top:102px;font-size:13.5px">Sign up or our newsletter below to keep in touch with our community</p>
  <div class="abs field" style="left:604px;top:143px;width:219px">First Name</div>
  <div class="abs field" style="left:830px;top:143px;width:218px">Last Name</div>
  <div class="abs field" style="left:604px;top:190px;width:219px">Email Address</div>
  <div class="abs signup" style="left:830px;top:190px;width:218px">SIGN UP</div>

  <div class="abs footer-text" style="left:0;top:278px;width:1200px;text-align:center;font-size:14.5px">© 2022 Dultavo. All Rights Reserved</div>
  <div class="abs" style="left:489px;top:321px;display:flex;gap:7px">
    <div class="pay-badge" style="background:#3b7bbf"></div>
    <div class="pay-badge" style="background:#2e6fb8"></div>
    <div class="pay-badge" style="background:#b9b9b9"></div>
    <div class="pay-badge" style="background:#8f8f8f"></div>
    <div class="pay-badge" style="background:#111;border:1px solid #666"></div>
    <div class="pay-badge" style="background:#e9e9e9"></div>
  </div>
</footer>

</body>
</html>
```